Kelo Wave Mint Business cards

Logo, tag line and photo on card
Agent Name
Title
Address
Phone number
Email
Website
Make logo on one side large by rotating  to portrait format.  Keep the background of the logo white.

Contact Information for Business Card
Slogan; Making Every Wave Count

```html
<!DOCTYPE html>
<html lang="en">
<head>
<meta charset="UTF-8">
<title>Kelo Wave Mint – Business Cards</title>
<link href="https://fonts.googleapis.com/css2?family=Montserrat:wght@400;700;800&display=swap" rel="stylesheet">
<style>
  :root {
    --navy: #0d2a6b;
    --red: #c8141e;
    --ink: #1c1c1c;
    --paper: #ffffff;
    --backdrop: #3a3a3a;
    --faint-navy: #e6e9f1;
  }
  * { margin: 0; padding: 0; box-sizing: border-box; }
  html, body { width: 1200px; height: 694px; overflow: hidden; }
  body {
    background: var(--backdrop);
    font-family: "Montserrat", sans-serif;
    position: relative;
  }
  .card {
    position: absolute;
    top: 187px;
    width: 560px;
    height: 320px;
    background: var(--paper);
    overflow: hidden;
  }
  .card--front { left: 27px; }
  .card--back { left: 613px; }

  /* Front side */
  .front-wordmark {
    position: absolute;
    left: 40px;
    top: 160px;
    transform-origin: 0 0;
    transform: rotate(-90deg) translate(-110px, 0);
    display: flex;
    align-items: center;
    gap: 14px;
  }
  .wordmark-square {
    width: 22px; height: 22px;
    background: var(--red);
    flex: none;
  }
  .wordmark-text {
    color: var(--navy);
    font-weight: 800;
    line-height: 0.95;
  }
  .front-wordmark .wordmark-text { font-size: 62px; }
  .front-decoration {
    position: absolute;
    right: -10px;
    top: 22px;
    color: var(--faint-navy);
    font-weight: 800;
    font-size: 86px;
    line-height: 0.92;
    text-align: right;
  }

  /* Back side */
  .back-wordmark {
    position: absolute;
    right: 40px;
    top: 34px;
    display: flex;
    align-items: flex-start;
    gap: 10px;
  }
  .back-wordmark .wordmark-square { width: 14px; height: 14px; margin-top: 6px; }
  .back-wordmark .wordmark-text { font-size: 34px; }
  .rule {
    position: absolute;
    height: 1px;
    background: var(--ink);
  }
  .rule--upper { right: 30px; top: 165px; width: 300px; }
  .rule--lower { left: 30px; top: 240px; width: 230px; }
  .person { position: absolute; left: 30px; top: 184px; }
  .person-name {
    color: var(--navy);
    font-weight: 700;
    font-size: 24px;
    letter-spacing: 0.5px;
  }
  .person-title {
    color: var(--ink);
    font-size: 13px;
    letter-spacing: 1px;
    margin-top: 2px;
  }
  .contact-list {
    position: absolute;
    left: 30px;
    top: 250px;
    list-style: none;
  }
  .contact-list li {
    display: flex;
    align-items: center;
    gap: 10px;
    font-size: 13px;
    color: var(--ink);
    height: 20px;
  }
  .contact-list svg { width: 14px; height: 14px; flex: none; }
  .address {
    position: absolute;
    right: 30px;
    top: 178px;
    text-align: right;
    font-size: 13px;
    line-height: 1.5;
    color: var(--ink);
  }
</style>
</head>
<body>

  <section class="card card--front" aria-label="Card front">
    <div class="front-decoration" aria-hidden="true">Kelo<br>Wave<br>Mint</div>
    <div class="front-wordmark">
      <span class="wordmark-square"></span>
      <span class="wordmark-text">Kelo<br>Wave<br>Mint</span>
    </div>
  </section>

  <section class="card card--back" aria-label="Card back">
    <div class="back-wordmark">
      <span class="wordmark-square"></span>
      <span class="wordmark-text">Kelo<br>Wave<br>Mint</span>
    </div>
    <div class="rule rule--upper"></div>

    <div class="person">
      <p class="person-name">DANIEL HARPER</p>
      <p class="person-title">MANAGING DIRECTOR</p>
    </div>
    <div class="rule rule--lower"></div>

    <ul class="contact-list">
      <li>
        <svg viewBox="0 0 24 24" aria-hidden="true"><path fill="#c8141e" d="M6.6 10.8a15 15 0 0 0 6.6 6.6l2.2-2.2a1 1 0 0 1 1-.25 11.4 11.4 0 0 0 3.6.57 1 1 0 0 1 1 1V20a1 1 0 0 1-1 1A17 17 0 0 1 3 4a1 1 0 0 1 1-1h3.5a1 1 0 0 1 1 1c0 1.25.2 2.45.57 3.6a1 1 0 0 1-.25 1z"/></svg>
        055-318 742 960
      </li>
      <li>
        <svg viewBox="0 0 24 24" aria-hidden="true"><rect x="2" y="5" width="20" height="14" fill="#c8141e"/><path d="M2 5l10 8 10-8" fill="none" stroke="#fff" stroke-width="2"/></svg>
        hello@kelowavemint.com
      </li>
      <li>
        <svg viewBox="0 0 24 24" aria-hidden="true"><g fill="none" stroke="#c8141e" stroke-width="2"><circle cx="12" cy="12" r="10"/><ellipse cx="12" cy="12" rx="4" ry="10"/><path d="M2 12h20"/></g></svg>
        www.kelowavemint.com
      </li>
    </ul>

    <p class="address">421, Address line goes here<br>45452, Country name</p>
  </section>

</body>
</html>
```